business card Calvanto

Wee need a business card design for a new compagny based on Paris
We developped innovative a platform for selling services to refresh, beautify and develop its housing.
We would like a red logo on a black background
Te final design should communicate quality service, know-how, high-end

Target Market(s)

individuals

Industry/Entity Type

Business

```html
<!DOCTYPE html>
<html lang="en">
<head>
<meta charset="utf-8">
<title>Calvanto — Business Card</title>
<link rel="stylesheet" href="https://fonts.googleapis.com/css2?family=Questrial&family=Open+Sans:wght@400;600;700&display=swap">
<style>
  :root {
    --backdrop: #e3e3e3;
    --card: #ffffff;
    --brand-red: #e2635b;
    --brand-red-soft: #ec7d75;
    --ink: #1f1f1f;
    --wordmark-grey: #7a7a7a;
    --text-dark: #2a2a2a;
    --divider: #ececec;
    --band-black: #141414;
  }
  * { box-sizing: border-box; margin: 0; padding: 0; }
  html, body {
    width: 1200px; height: 852px; overflow: hidden;
    background: var(--backdrop);
  }
  .sheet {
    width: 1200px; height: 852px;
    display: flex; flex-direction: column; align-items: center; justify-content: center;
    gap: 44px;
  }
  .card {
    position: relative;
    width: 630px; height: 360px;
    background: var(--card);
    border-radius: 24px;
    overflow: hidden;
    box-shadow: 0 6px 18px rgba(0,0,0,0.12);
  }
  .brand {
    position: absolute;
    display: flex; align-items: center; gap: 16px;
  }
  .brand-square {
    background: var(--brand-red);
    flex: none;
  }
  .brand-name {
    font-family: "Questrial", sans-serif;
    color: var(--wordmark-grey);
    font-weight: 400;
    letter-spacing: 0.5px;
  }
  /* Front */
  .card-front .brand { left: 150px; top: 142px; }
  .card-front .brand-square { width: 72px; height: 72px; }
  .card-front .brand-name { font-size: 62px; line-height: 1; }

  /* Back */
  .card-back .brand { left: 40px; top: 170px; gap: 12px; }
  .card-back .brand-square { width: 50px; height: 50px; }
  .card-back .brand-name { font-size: 44px; line-height: 1; }
  .divider {
    position: absolute; left: 300px; top: 0; width: 1px; height: 300px;
    background: var(--divider);
  }
  .contact {
    position: absolute; left: 330px; top: 48px;
    font-family: "Open Sans", sans-serif; color: var(--text-dark);
  }
  .contact-name {
    font-size: 19px; font-weight: 700; color: var(--brand-red); line-height: 1.1;
  }
  .contact-title { font-size: 11px; margin-top: 3px; margin-left: 16px; }
  .contact-list { list-style: none; margin-top: 30px; }
  .contact-list li {
    display: flex; align-items: flex-start; gap: 9px;
    font-size: 13.5px; line-height: 19px;
  }
  .contact-list svg { width: 12px; height: 12px; margin-top: 4px; flex: none; fill: var(--brand-red); }
  .contact-list .no-icon { padding-left: 21px; }
  .card-band { position: absolute; left: 0; bottom: 0; width: 630px; height: 58px; }
  .band-url {
    position: absolute; right: 36px; bottom: 17px;
    font-family: "Open Sans", sans-serif; font-size: 14px; color: #ffffff; letter-spacing: 0.3px;
  }
  .band-url .accent { color: var(--brand-red); }
</style>
</head>
<body>
<main class="sheet">
  <section class="card card-front" aria-label="Card front">
    <div class="brand">
      <span class="brand-square"></span>
      <span class="brand-name">Calvanto</span>
    </div>
  </section>

  <section class="card card-back" aria-label="Card back">
    <div class="brand">
      <span class="brand-square"></span>
      <span class="brand-name">Calvanto</span>
    </div>
    <span class="divider"></span>
    <div class="contact">
      <p class="contact-name">Your Long Name</p>
      <p class="contact-title">Managing Director</p>
      <ul class="contact-list">
        <li><svg viewBox="0 0 12 12" aria-hidden="true"><path d="M2.5 1h2l1 2.5-1.2 1a7 7 0 0 0 3.2 3.2l1-1.2L11 7.5v2A1.5 1.5 0 0 1 9.5 11 8.5 8.5 0 0 1 1 2.5 1.5 1.5 0 0 1 2.5 1z"/></svg>00.00.00.0000</li>
        <li><svg viewBox="0 0 12 12" aria-hidden="true"><path d="M3.5 0.5h5a1 1 0 0 1 1 1v9a1 1 0 0 1-1 1h-5a1 1 0 0 1-1-1v-9a1 1 0 0 1 1-1zM4 2v6.5h4V2zM6 9.3a.7.7 0 1 0 0 1.4.7.7 0 0 0 0-1.4z"/></svg>00.00.00.0000</li>
        <li><svg viewBox="0 0 12 12" aria-hidden="true"><path d="M1 2.5h10v7H1zM1.6 3.1 6 6.4l4.4-3.3z" fill-rule="evenodd"/></svg>yourname@yourwebsite.com</li>
        <li><svg viewBox="0 0 12 12" aria-hidden="true"><path d="M6 0.5a3.8 3.8 0 0 1 3.8 3.8C9.8 7 6 11.5 6 11.5S2.2 7 2.2 4.3A3.8 3.8 0 0 1 6 .5zm0 2.3a1.5 1.5 0 1 0 0 3 1.5 1.5 0 0 0 0-3z"/></svg>Your Commercial or office address</li>
        <li class="no-icon">in just two line with pincode</li>
      </ul>
    </div>
    <svg class="card-band" viewBox="0 0 630 58" preserveAspectRatio="none" aria-hidden="true">
      <rect x="0" y="44" width="440" height="14" fill="var(--brand-red-soft)"/>
      <polygon points="440,0 630,0 630,58 424,58" fill="var(--band-black)"/>
    </svg>
    <p class="band-url">www.<span class="accent">yourwebsite</span>.com</p>
  </section>
</main>
</body>
</html>
```